Career-focused learning application platform

We have a K-12 learning application platform designed for grades 6-12 that needs user interface improvements that provide a positive experience for all users (teachers and students). The learning platform provides career-focused math curriculum and career exploration resources. We would like to improve the user-interface with engaging design elements without taking away from the functionality and performance of the platform.

```html
<!DOCTYPE html>
<html lang="en">
<head>
<meta charset="utf-8">
<title>Routewise Careers – Learning Platform Screens</title>
<link href="https://fonts.googleapis.com/css2?family=Roboto:wght@300;400;500;700&display=swap" rel="stylesheet">
<style>
:root{
  --page:#fdf3e8;
  --surface:#fef7f0;
  --white:#ffffff;
  --orange:#f47f1b;
  --orange-deep:#ef6f12;
  --ink:#2b2b2b;
  --muted:#6b6b6b;
  --dark:#262626;
  --line:#e6e0da;
  --teal:#1c5c73;
  --navy:#253a6b;
}
*{box-sizing:border-box;margin:0;padding:0}
html,body{width:1200px;height:1060px;overflow:hidden}
body{background:var(--page);font-family:'Roboto',sans-serif;color:var(--ink);position:relative}
.panel{position:absolute;background:var(--surface);box-shadow:0 2px 8px rgba(0,0,0,.12);overflow:hidden}
.abs{position:absolute}
.site-header{position:absolute;left:0;top:0;width:100%;height:59px;background:var(--white);box-shadow:0 1px 3px rgba(0,0,0,.06)}
.brand{position:absolute;left:18px;top:18px;display:flex;align-items:center;gap:4px}
.brand-dot{width:12px;height:12px;border-radius:50%;background:var(--orange)}
.brand-name{font-size:8.5px;font-weight:700;color:var(--orange);letter-spacing:.2px}
.nav{position:absolute;top:25px;font-size:6.4px;font-weight:500;color:var(--ink);white-space:nowrap}
.nav.active{color:var(--orange)}
.nav-user{position:absolute;top:24px;left:455px;font-size:6.4px;color:var(--orange);display:flex;align-items:center;gap:3px}
.footer{position:absolute;left:0;width:100%;height:32px;background:var(--dark);color:#fff;font-size:7px;text-align:center;line-height:32px}
.footer .code{position:absolute;right:16px;top:7px;font-size:6.5px}
.btn{position:absolute;display:flex;align-items:center;justify-content:center;background:var(--orange);color:#fff;border-radius:2px;white-space:nowrap}
.btn-outline{background:#fff;color:var(--orange);border:1px solid var(--orange)}
.pill{border-radius:11px;font-size:7px}
/* sign-in */
.signin-card{position:absolute;left:18px;top:70px;width:496px;height:286px;background:#fff;border:1px solid #f1ebe5;border-radius:3px}
.signin-title{position:absolute;left:0;width:290px;text-align:center;font-size:17px;font-weight:300;color:#333}
.signin-sub{position:absolute;left:0;width:290px;text-align:center;font-size:12px;font-weight:500;color:var(--orange)}
.label{position:absolute;font-size:6px;color:#444}
.field{position:absolute;width:195px;height:21px;border:1px solid #d8d8d8;border-radius:2px;background:#fff}
.art{position:absolute;border-radius:3px}
/* class page */
.class-card{position:absolute;left:18px;top:83px;width:496px;height:329px;background:#fff;border-radius:4px;box-shadow:0 0 4px rgba(0,0,0,.08);overflow:hidden}
.class-head{position:absolute;left:0;top:0;width:100%;height:59px;background:var(--dark);color:#fff;font-size:8.3px;line-height:12.5px;padding:11px 13px}
.tab{position:absolute;font-size:8.5px;color:#333}
.accordion{position:absolute;left:10px;top:107px;width:476px;height:203px;border:1px solid #eee;border-radius:4px;overflow:hidden}
.acc-head{height:28px;background:var(--orange);color:#fff;font-size:8.5px;display:flex;align-items:center;padding-left:9px;position:relative}
.lesson{position:relative;height:43.5px;border-bottom:1px solid #ececec}
.lesson-thumb{position:absolute;left:10px;top:11px;width:16px;height:16px;border-radius:2px;background:linear-gradient(160deg,var(--navy) 40%,var(--orange) 41%)}
.lesson-title{position:absolute;left:40px;top:8px;font-size:6.2px;font-weight:500;color:#222}
.lesson-desc{position:absolute;left:40px;top:19px;width:320px;font-size:5.1px;line-height:8px;color:#555}
.lesson-due{position:absolute;right:10px;top:9px;font-size:5.2px;color:#333}
.begin{position:absolute;left:403px;top:19px;width:46px;height:13px;font-size:5.3px;border-radius:2px}
.gear{position:absolute;left:453px;top:19px;width:15px;height:13px;background:#555;border-radius:2px;display:flex;align-items:center;justify-content:center}
/* home */
.spotlight{position:absolute;left:18px;top:83px;width:496px;height:251px;border-radius:5px;overflow:hidden;background:linear-gradient(135deg,#f7891f 0%,#f27a17 60%,#ef6c10 100%)}
.spot-head{height:30px;background:var(--dark);color:#fff;font-size:12px;padding-left:13px;line-height:30px}
.spot-text{position:absolute;color:#fff}
.section-title{position:absolute;font-size:17px;color:#222}
.course{position:absolute;top:387px;width:155px;height:175px;background:#fff;border:1.5px solid #f5b27a;border-radius:4px;text-align:center}
.cover{position:absolute;left:46px;top:15px;width:62px;height:60px;border-radius:2px}
.course-role{position:absolute;left:0;width:100%;top:90px;font-size:8px;font-weight:500;color:#222}
.course-period{position:absolute;left:0;width:100%;top:102px;font-size:8px;color:var(--orange)}
.course-sub{position:absolute;left:0;width:100%;top:115px;font-size:6.2px;color:#555}
table{position:absolute;left:18px;top:630px;width:437px;border-collapse:collapse;background:#fff;font-size:7.6px;color:#444;border-radius:4px;overflow:hidden}
th{background:var(--orange);color:#fff;font-weight:500;text-align:left;height:28px;padding-left:13px;font-size:8.2px}
td{height:31px;padding-left:13px;border-bottom:1px solid #ececec;border-right:1px solid #ececec}
td:last-child{border-right:none}
</style>
</head>
<body>

<!-- Sign in screen -->
<section class="panel" style="left:48px;top:52px;width:532px;height:426px">
  <div class="brand"><span class="brand-dot"></span><span class="brand-name">ROUTEWISE CAREERS</span></div>
  <div class="btn btn-outline" style="left:415px;top:23px;width:45px;height:18px;font-size:6.4px">➜ SIGN IN</div>
  <div class="btn" style="left:466px;top:23px;width:49px;height:18px;font-size:6.4px">✎ REGISTER</div>

  <div class="signin-card">
    <div class="signin-title" style="left:-18px;top:31px">SIGN IN WITH YOUR</div>
    <div class="signin-sub" style="left:-18px;top:55px">SCHOOL ACCOUNT</div>
    <div class="btn" style="left:58px;top:83px;width:66px;height:22px;font-size:7.8px"><span style="width:7px;height:7px;background:#fff;margin-right:5px"></span>Tessera</div>
    <div class="btn" style="left:129px;top:83px;width:66px;height:22px;font-size:7.8px;background:#3a3a3a">Gleam</div>
    <div class="abs" style="left:45px;top:128px;width:166px;height:1px;background:#ddd"></div>
    <div class="abs" style="left:98px;top:123px;padding:0 4px;background:#fff;font-size:6px;color:#444">Or continue with</div>
    <div class="label" style="left:31px;top:134px">Email Address</div>
    <div class="field" style="left:29px;top:147px"></div>
    <div class="label" style="left:31px;top:177px">Password</div>
    <div class="field" style="left:29px;top:189px"></div>
    <div class="abs" style="left:29px;top:216px;width:9px;height:9px;border:1px solid #ccc;border-radius:2px"></div>
    <div class="label" style="left:43px;top:217px">Remember me</div>
    <div class="btn" style="left:29px;top:236px;width:52px;height:19px;font-size:6.6px">SIGN IN</div>
    <div class="label" style="left:196px;top:242px;color:#333">Need an Account?</div>
    <div class="btn" style="left:192px;top:252px;width:64px;height:19px;font-size:5.8px;background:#fff;color:#444;border:1px solid #ccc">REGISTER HERE</div>
    <div class="art" role="img" aria-label="Illustration of a student studying at a desk surrounded by books" style="left:267px;top:7px;width:223px;height:274px;background:radial-gradient(circle at 50% 60%,#2a6f86 0%,var(--teal) 70%)">
      <div style="position:absolute;top:52px;width:100%;text-align:center;color:#fff;font-size:10px;font-weight:700">ROUTEWISE CAREERS</div>
    </div>
  </div>

  <footer class="footer" style="top:394px">© Copyright 2021 Routewise Careers.All Rights Reserved<span class="code">C2</span></footer>
</section>

<!-- Class detail screen -->
<section class="panel" style="left:48px;top:519px;width:532px;height:465px">
  <header class="site-header">
    <div class="brand"><span class="brand-dot"></span><span class="brand-name">ROUTEWISE CAREERS</span></div>
    <span class="nav active" style="left:228px">HOME</span>
    <span class="nav" style="left:270px">CAREER TOOLS</span>
    <span class="nav" style="left:339px">CLASSES</span>
    <span class="nav" style="left:389px">ASSESSMENTS</span>
    <span class="nav-user"><svg width="7" height="7" viewBox="0 0 10 10" fill="none" stroke="#f47f1b"><circle cx="5" cy="3" r="2.2"/><path d="M1 9.5c0-2.5 2-3.8 4-3.8s4 1.3 4 3.8z"/></svg>r.moss@quillbay.org</span>
  </header>

  <div class="class-card">
    <div class="class-head">Math Teacher<br>Period 1<br>8th Grade Math / Pre -Algebra</div>
    <div class="btn" style="left:334px;top:18px;width:69px;height:20px;font-size:8px">Class Roster</div>
    <div class="btn" style="left:410px;top:18px;width:73px;height:20px;font-size:8px">⚙ Class Settings</div>
    <span class="tab" style="left:171px;top:77px">Lessions</span>
    <div class="abs" style="left:169px;top:91px;width:39px;height:1.5px;background:var(--orange)"></div>
    <span class="tab" style="left:299px;top:77px">Scores</span>

    <div class="accordion">
      <div class="acc-head">⌄&nbsp; Upcoming Lessons
        <div class="btn" style="left:412px;top:6px;width:56px;height:16px;background:#fff;color:#333;font-size:5.6px">● ADD LESSON</div>
      </div>
      <div class="lesson"><div class="lesson-thumb"></div><div class="lesson-title">1.1 : Translations</div><div class="lesson-desc">Sed ut perspiciatis unde omnis iste natus error sit voluptatem accusantium doloremque laudantium, totam rem aperiam, eaque ipsa quae ab illo inventore veritatis et quasi architecto beatae vitae dicta sunt explicabo.</div><div class="lesson-due">Due : 10/18 at 11:59 Pm</div><div class="btn begin">Begin Lesson</div><div class="gear"><svg width="6" height="6" viewBox="0 0 10 10"><circle cx="5" cy="5" r="3.5" fill="#fff"/><circle cx="5" cy="5" r="1.4" fill="#555"/></svg></div></div>
      <div class="lesson"><div class="lesson-thumb"></div><div class="lesson-title">201:Operations With Rational Number</div><div class="lesson-desc">Sed ut perspiciatis unde omnis iste natus error sit voluptatem accusantium doloremque laudantium, totam rem aperiam, eaque ipsa quae ab illo inventore veritatis et quasi architecto beatae vitae dicta sunt explicabo.</div><div class="lesson-due">Due : 10/18 at 11:59 Pm</div><div class="btn begin">Begin Lesson</div><div class="gear"><svg width="6" height="6" viewBox="0 0 10 10"><circle cx="5" cy="5" r="3.5" fill="#fff"/><circle cx="5" cy="5" r="1.4" fill="#555"/></svg></div></div>
      <div class="lesson"><div class="lesson-thumb"></div><div class="lesson-title">3.1:Paralle Lines and Transversals</div><div class="lesson-desc">Sed ut perspiciatis unde omnis iste natus error sit voluptatem accusantium doloremque laudantium, totam rem aperiam, eaque ipsa quae ab illo inventore veritatis et quasi architecto beatae vitae dicta sunt explicabo.</div><div class="lesson-due">Due : 10/18 at 11:59 Pm</div><div class="btn begin">Begin Lesson</div><div class="gear"><svg width="6" height="6" viewBox="0 0 10 10"><circle cx="5" cy="5" r="3.5" fill="#fff"/><circle cx="5" cy="5" r="1.4" fill="#555"/></svg></div></div>
      <div class="lesson" style="border-bottom:none"><div class="lesson-thumb"></div><div class="lesson-title">3.3:Angel Relationships In Triangles</div><div class="lesson-desc">Sed ut perspiciatis unde omnis iste natus error sit voluptatem accusantium doloremque laudantium, totam rem aperiam, eaque ipsa quae ab illo inventore veritatis et quasi architecto beatae vitae dicta sunt explicabo.</div><div class="lesson-due">Due : 10/18 at 11:59 Pm</div><div class="btn begin">Begin Lesson</div><div class="gear"><svg width="6" height="6" viewBox="0 0 10 10"><circle cx="5" cy="5" r="3.5" fill="#fff"/><circle cx="5" cy="5" r="1.4" fill="#555"/></svg></div></div>
    </div>
  </div>

  <footer class="footer" style="top:433px">© Copyright 2021 Routewise Careers.All Rights Reserved<span class="code">C2</span></footer>
</section>

<!-- Home dashboard screen -->
<section class="panel" style="left:610px;top:52px;width:532px;height:836px">
  <header class="site-header">
    <div class="brand"><span class="brand-dot"></span><span class="brand-name">ROUTEWISE CAREERS</span></div>
    <span class="nav active" style="left:229px">HOME</span>
    <span class="nav" style="left:270px">CAREER TOOLS</span>
    <span class="nav" style="left:339px">CLASSES</span>
    <span class="nav" style="left:389px">ASSESSMENTS</span>
    <span class="nav-user"><svg width="7" height="7" viewBox="0 0 10 10" fill="none" stroke="#f47f1b"><circle cx="5" cy="3" r="2.2"/><path d="M1 9.5c0-2.5 2-3.8 4-3.8s4 1.3 4 3.8z"/></svg>r.moss@quillbay.org</span>
  </header>

  <div class="spotlight">
    <div class="spot-head">Career Spotlight</div>
    <div class="spot-text" style="left:13px;top:54px;font-size:11.5px;font-weight:700">Plumbers, Pipefitters &amp; Steamfitters</div>
    <div class="spot-text" style="left:13px;top:85px;font-size:12px;font-weight:300">What they do</div>
    <div class="spot-text" style="left:13px;top:110px;width:220px;font-size:5.6px;line-height:11px;opacity:.92">Sed ut perspiciatis unde omnis iste natus error sit voluptatem accusantium doloremque laudantium, totam rem aperiam, eaque ipsa quae ab illo inventore veritatis et quasi architecto beatae vitae dicta sunt explicabo.</div>
    <div class="spot-text" style="left:13px;top:155px;font-size:12px;font-weight:300">Earnings</div>
    <div class="spot-text" style="left:13px;top:179px;font-size:6.4px">Low End</div>
    <div class="spot-text" style="left:72px;top:179px;font-size:6.4px">Medium</div>
    <div class="spot-text" style="left:131px;top:179px;font-size:6.4px">High End</div>
    <div class="spot-text" style="left:13px;top:193px;font-size:6.4px">$33,460</div>
    <div class="spot-text" style="left:72px;top:193px;font-size:6.4px">$56,330</div>
    <div class="spot-text" style="left:131px;top:193px;font-size:6.4px">$98,990</div>
    <div class="abs" role="img" aria-label="Video still of a plumber with tools beside a kitchen sink" style="left:245px;top:53px;width:233px;height:171px;background:linear-gradient(90deg,#d9d6d0 0%,#b9b6b0 45%,#2f4a7a 70%,#22365c 100%)">
      <svg class="abs" style="left:98px;top:67px" width="38" height="38" viewBox="0 0 38 38"><circle cx="19" cy="19" r="17" fill="rgba(0,0,0,.35)" stroke="#fff" stroke-width="2"/><path d="M15 12l12 7-12 7z" fill="#fff"/></svg>
    </div>
  </div>

  <div class="section-title" style="left:18px;top:358px">Classes</div>
  <div class="abs" style="left:479px;top:366px;font-size:6.4px;color:var(--orange);text-decoration:underline">View All »</div>

  <div class="course" style="left:18px">
    <div class="cover" role="img" aria-label="Course cover art for 8th Grade Math / Pre-Algebra" style="background:linear-gradient(180deg,var(--navy) 0 45%,var(--orange) 45% 100%)"></div>
    <div class="course-role">MATH TEACHER</div><div class="course-period">Period 1</div><div class="course-sub">8th Grade Math / Pre-Algebra</div>
    <div class="btn pill" style="left:44px;top:135px;width:66px;height:21px">Go to Class</div>
  </div>
  <div class="course" style="left:188px">
    <div class="cover" role="img" aria-label="Course cover art for Algebra I" style="background:linear-gradient(180deg,#5a2350 0 45%,var(--orange) 45% 100%)"></div>
    <div class="course-role">MATH TEACHER</div><div class="course-period">Period 6</div><div class="course-sub">Algebra 1</div>
    <div class="btn pill" style="left:44px;top:135px;width:66px;height:21px">Go to Class</div>
  </div>
  <div class="course" style="left:358px">
    <div class="cover" role="img" aria-label="Course cover art for Algebra I" style="background:linear-gradient(180deg,#5a2350 0 45%,var(--orange) 45% 100%)"></div>
    <div class="course-role">MATH TEACHER</div><div class="course-period">Period 5</div><div class="course-sub">Algebra 1</div>
    <div class="btn pill" style="left:44px;top:135px;width:66px;height:21px">Go to Class</div>
  </div>

  <div class="section-title" style="left:18px;top:587px">Upcoming Lessons</div>
  <div class="abs" style="left:18px;top:610px;font-size:6.4px;color:#333">Lessons due up to the next 7 days :</div>

  <table>
    <thead><tr><th style="width:123px">CLASS</th><th style="width:166px">LESSON</th><th>DUE</th></tr></thead>
    <tbody>
      <tr><td>Period 1</td><td>1-1 - Transiations</td><td>Otober 15th at 11:59PM</td></tr>
      <tr><td>Period 1</td><td>2-1 Operations with Rational Numbers</td><td>Otober 18th at 11:59PM</td></tr>
      <tr><td>Period 1</td><td>3-1- Parallel Lines and Transversals</td><td>Otober 19th at 11:59PM</td></tr>
      <tr><td style="border-bottom:none">Period 1</td><td style="border-bottom:none">3-3-Angle Relationships Triangles</td><td style="border-bottom:none">Otober 21th at 11:59PM</td></tr>
    </tbody>
  </table>

  <footer class="footer" style="top:805px;height:31px;line-height:31px">© Copyright 2021 Routewise Careers.All Rights Reserved<span class="code">C2</span></footer>
</section>

</body>
</html>
```